Handyman business card & stationary
Your Home Maintenance Specialist
Handyman business card & stationary - Construction
Creative Brief
Bright & Fun-filled
Dale Kowronski
Owner
4873 Maplecrest Lane Wylie, Texas 75214
Dale@steadyfixhomecare.example
steadyfixhomecare.example
Bonded and Insured
Your Home Maintenance Specialist Call of for a free estimate 214-555-0187

```html
<!DOCTYPE html>
<html lang="en">
<head>
<meta charset="utf-8">
<title>SteadyFix Home Care – Business Card</title>
<link href="https://fonts.googleapis.com/css2?family=Montserrat:wght@400;500;600;700&display=swap" rel="stylesheet">
<style>
  :root {
    --navy: #2f2a7d;
    --navy-deep: #26216a;
    --red: #d8232a;
    --sky: #3d8fd1;
    --ink: #3a3a4a;
    --paper: #ffffff;
    --backdrop: #cfcfcf;
  }
  * { box-sizing: border-box; margin: 0; padding: 0; }
  html, body { width: 1200px; height: 857px; overflow: hidden; }
  body {
    background: var(--backdrop);
    font-family: "Montserrat", sans-serif;
    display: flex;
    align-items: center;
    justify-content: center;
    gap: 60px;
  }
  .card {
    width: 520px;
    height: 297px;
    position: relative;
    overflow: hidden;
    box-shadow: 0 6px 18px rgba(0,0,0,.18);
  }

  /* Front */
  .card-front { background: var(--paper); border-bottom: 3px solid var(--red); }
  .front-name {
    position: absolute; top: 44px; right: 40px;
    color: var(--navy); font-weight: 700; font-size: 20px;
  }
  .front-role {
    position: absolute; top: 72px; right: 40px;
    color: var(--red); font-weight: 500; font-size: 11px; letter-spacing: .08em;
  }
  .front-brand {
    position: absolute; left: 36px; top: 100px;
    display: flex; align-items: center; gap: 8px;
    color: var(--navy); font-weight: 700; font-size: 19px; letter-spacing: .02em;
  }
  .brand-dot { width: 12px; height: 12px; border-radius: 50%; background: var(--sky); }
  .front-rule {
    position: absolute; left: 36px; right: 36px; top: 150px;
    height: 1px; background: var(--red);
  }
  .front-address {
    position: absolute; left: 36px; top: 168px;
    color: var(--ink); font-size: 11px; line-height: 1.6;
  }
  .front-contact {
    position: absolute; left: 220px; top: 168px;
    color: var(--ink); font-size: 11px; line-height: 1.6;
    list-style: none;
  }
  .front-contact li { display: flex; align-items: center; gap: 6px; }
  .front-contact svg { width: 11px; height: 11px; fill: var(--navy); }
  .front-band {
    position: absolute; left: 0; right: 0; bottom: 0; height: 44px;
    background: var(--navy);
    display: flex; align-items: center; padding-left: 36px;
    color: #fff; font-size: 11px; letter-spacing: .04em;
  }
  .front-band::before {
    content: ""; position: absolute; left: 0; right: 0; top: -4px; height: 2px; background: var(--red);
  }

  /* Back */
  .card-back {
    background: var(--navy);
    border-bottom: 3px solid var(--red);
    color: #fff; text-align: center;
    display: flex; flex-direction: column; align-items: center; justify-content: center;
  }
  .back-brand {
    font-weight: 700; font-size: 22px; letter-spacing: .03em;
    color: rgba(255,255,255,.35);
    display: flex; align-items: center; gap: 8px;
    margin-bottom: 20px;
  }
  .back-brand .brand-dot { background: rgba(255,255,255,.35); }
  .back-tagline { font-size: 13px; font-weight: 500; }
  .back-call { font-size: 12px; margin-top: 4px; opacity: .9; }
  .back-phone { font-size: 34px; font-weight: 600; margin-top: 14px; letter-spacing: .02em; }
</style>
</head>
<body>
  <section class="card card-front">
    <div class="front-name">Dale Kowronski</div>
    <div class="front-role">OWNER</div>
    <div class="front-brand"><span class="brand-dot"></span>SteadyFix Home Care</div>
    <div class="front-rule"></div>
    <address class="front-address">
      4873 Maplecrest Lane<br>Wylie, Texas 75214
    </address>
    <ul class="front-contact">
      <li><svg viewBox="0 0 24 24"><path d="M6.6 10.8a15.1 15.1 0 0 0 6.6 6.6l2.2-2.2a1 1 0 0 1 1-.25 11.4 11.4 0 0 0 3.6.57 1 1 0 0 1 1 1V20a1 1 0 0 1-1 1A17 17 0 0 1 3 4a1 1 0 0 1 1-1h3.5a1 1 0 0 1 1 1c0 1.25.2 2.45.57 3.57a1 1 0 0 1-.25 1z"/></svg>214-555-0187</li>
      <li><svg viewBox="0 0 24 24"><path d="M2 5h20v14H2zm2 2v.5l8 5 8-5V7z"/></svg>Dale@steadyfixhomecare.example</li>
    </ul>
    <div class="front-band">steadyfixhomecare.example</div>
  </section>

  <section class="card card-back">
    <div class="back-brand"><span class="brand-dot"></span>SteadyFix Home Care</div>
    <p class="back-tagline">Your Home Maintenance Specialist</p>
    <p class="back-call">Call of for a free estimate</p>
    <p class="back-phone">214-555-0187</p>
  </section>
</body>
</html>
```